Automotive eCommerce Business looking for a business card design

Looking for a clean and simple business card design. Our company name is "Brindle Auto" and we are a company specializing in the ecommerce sales of automotive parts, specifically for pick up trucks and large SUVs. Our company colours are red, black, and white.

Feel free to use the logo provided or create a new logo that you seem fit. Looking forward to your creative ideas!

Industry/Entity Type

Automotive

Contact Information for Business Card

We were thinking of a possibly two-sided design featuring just the logo and company name on one side, and personal information on the other side. Single sided designs will be considered as well.

Font styles to use
Serif
Sans Serif
Decorative

Colors
ec1f27
ffffff
000000

Requirements
Must have
• Space for employee's name, title, phone number and email address, along with the company address and website somewhere.

```html
<!DOCTYPE html>
<html lang="en">
<head>
<meta charset="utf-8">
<title>Brindle Auto – Business Cards</title>
<link href="https://fonts.googleapis.com/css2?family=Cinzel:wght@500;600&family=Roboto+Condensed:wght@400;700&family=Roboto:wght@300;400&display=swap" rel="stylesheet">
<style>
  :root {
    --brand-red: #a51c22;
    --brand-grey: #58595b;
    --card-white: #f7f7f7;
    --ink-dark: #3a3a3a;
    --ink-soft: #555555;
    --backdrop: #d9d9d9;
    --on-red: #ffffff;
  }
  * { box-sizing: border-box; margin: 0; padding: 0; }
  html, body { width: 1200px; height: 886px; overflow: hidden; }
  body {
    background: var(--backdrop);
    position: relative;
    font-family: "Roboto", sans-serif;
  }
  .card {
    position: absolute;
    background: var(--card-white);
    border-radius: 22px;
    overflow: hidden;
    box-shadow: 0 6px 18px rgba(0,0,0,0.18);
  }

  /* Front: brand side */
  .card-front {
    left: 70px; top: 283px;
    width: 560px; height: 320px;
    display: flex; flex-direction: column; align-items: center; justify-content: center;
  }
  .brand-mark {
    display: flex; align-items: center; gap: 12px;
    margin-bottom: 26px;
  }
  .brand-mark .mark-square {
    width: 26px; height: 26px; background: var(--brand-red);
  }
  .brand-mark .mark-name {
    font-family: "Cinzel", serif; font-weight: 600;
    font-size: 34px; color: var(--brand-red);
  }
  .company-name {
    font-family: "Cinzel", serif; font-weight: 500;
    font-size: 26px; color: var(--ink-dark); letter-spacing: 0.5px;
  }
  .company-web {
    margin-top: 22px;
    font-family: "Roboto", sans-serif; font-weight: 300;
    font-size: 14px; letter-spacing: 7px; color: var(--ink-soft);
  }

  /* Back: personal side */
  .card-back {
    left: 790px; top: 163px;
    width: 320px; height: 560px;
  }
  .band-grey {
    position: absolute; left: 0; right: 0; top: 44px; height: 120px;
    background: var(--brand-grey);
    display: flex; flex-direction: column; justify-content: center;
    padding-left: 30px;
  }
  .person-name {
    font-family: "Roboto Condensed", sans-serif; font-weight: 700;
    font-size: 30px; color: var(--on-red); letter-spacing: 0.5px;
  }
  .person-title {
    font-family: "Roboto Condensed", sans-serif; font-weight: 400;
    font-size: 15px; color: var(--on-red); margin-top: 4px;
  }
  .band-red {
    position: absolute; left: 0; right: 0; top: 164px; bottom: 44px;
    background: var(--brand-red);
    color: var(--on-red);
    font-family: "Roboto Condensed", sans-serif;
    display: flex; flex-direction: column; align-items: center;
  }
  .band-red .brand-name {
    font-family: "Roboto Condensed", sans-serif; font-weight: 700;
    font-size: 32px; margin-top: 44px; letter-spacing: 1px;
  }
  .address {
    margin-top: 46px; text-align: center; font-size: 16px; line-height: 1.35;
  }
  .divider {
    width: 30px; height: 2px; background: var(--on-red); margin: 16px 0;
  }
  .contact-list { list-style: none; font-size: 16px; line-height: 1.45; }
  .contact-list li { display: flex; align-items: center; gap: 8px; }
  .contact-list svg { width: 13px; height: 13px; flex: none; }
</style>
</head>
<body>

  <section class="card card-front" aria-label="Business card front">
    <div class="brand-mark">
      <span class="mark-square"></span>
      <span class="mark-name">Brindle Auto</span>
    </div>
    <h1 class="company-name">Brindle Auto Ltd.</h1>
    <p class="company-web">www.brindleauto.com</p>
  </section>

  <section class="card card-back" aria-label="Business card back">
    <div class="band-grey">
      <p class="person-name">OWEN HARTLEY</p>
      <p class="person-title">CEO/FOUNDER</p>
    </div>
    <div class="band-red">
      <p class="brand-name">Brindle Auto</p>
      <p class="address">412 Cedar Ridge Road<br>Fairbanks, Alaska 99701</p>
      <span class="divider"></span>
      <ul class="contact-list">
        <li><svg viewBox="0 0 16 16"><path fill="#fff" d="M3 1l3 3-1.5 2a9 9 0 0 0 5.5 5.5L12 10l3 3-2 2C7 15 1 9 1 3z"/></svg>555 210 4471</li>
        <li><svg viewBox="0 0 16 16"><rect x="4" y="1" width="8" height="14" rx="1.5" fill="none" stroke="#fff" stroke-width="1.6"/></svg>555 382 9016</li>
        <li><svg viewBox="0 0 16 16"><rect x="1" y="6" width="14" height="8" rx="1" fill="#fff"/><rect x="4" y="2" width="8" height="5" fill="none" stroke="#fff" stroke-width="1.4"/></svg>555 647 1253</li>
        <li><svg viewBox="0 0 16 16"><rect x="1" y="3" width="14" height="10" fill="#fff"/><path d="M1 3l7 6 7-6" fill="none" stroke="#a51c22" stroke-width="1.4"/></svg>owen@brindleauto.com</li>
        <li><svg viewBox="0 0 16 16"><circle cx="8" cy="8" r="7" fill="#fff"/><path d="M1 8h14M8 1c3 3 3 11 0 14M8 1c-3 3-3 11 0 14" fill="none" stroke="#a51c22" stroke-width="1"/></svg>www.brindleauto.com</li>
      </ul>
    </div>
  </section>

</body>
</html>
```